Classy, Elegant, Simple Business Card Design

Looking to have a classy, simple, and elegant design. Want a top notch designed business card. I really like the look of the new torvane credit card. I also like the design I attached. I am trying to reach 21-29 year old females for booking us for there wedding or event. We offer Disc Jockey Service, Photo Booth Rentals, and Uplighting .

Target Market(s)

21-28 year old females

Contact Information for Business Card

Has to have logo, website, email, and phone number

Font styles to use
Other font styles liked:
• open to font choice, modern, clean
Designer to choose
33a6d7
0791cd
0555a3
ffffff

Requirements
Must have
• Has to have logo, website, email, and phone number
Nice to have
• I really like the design of the new torvane credit card. I also included my logo and some designs I like
Should not have
• clutter or too much info

```html
<!DOCTYPE html>
<html lang="en">
<head>
<meta charset="utf-8">
<title>Lumavelle Event Group – Business Card</title>
<link rel="stylesheet" href="https://fonts.googleapis.com/css2?family=Roboto:wght@400;500&display=swap">
<style>
  :root {
    --sky: #33a6d7;
    --azure: #0791cd;
    --royal: #0555a3;
    --white: #ffffff;
    --card: #f1f1f1;
    --stage: #b9b9b9;
    --ink: #2a2a2a;
    --bars-grey: #c9c9c9;
  }
  * { box-sizing: border-box; margin: 0; padding: 0; }
  html, body {
    width: 1200px; height: 576px; overflow: hidden;
    background: var(--stage);
    font-family: "Roboto", Arial, sans-serif;
  }
  .canvas { position: relative; width: 1200px; height: 576px; }
  .card {
    position: absolute; top: 138px;
    width: 484px; height: 294px;
    background: var(--card);
    border-radius: 10px;
    overflow: hidden;
  }
  .card--front { left: 82px; }
  .card--back { left: 602px; }

  .brand-name {
    position: absolute; left: 0; right: 0;
    color: var(--royal);
    font-weight: 500;
    text-align: center;
    letter-spacing: 0.03em;
    white-space: nowrap;
  }
  .card--front .brand-name { top: 152px; font-size: 28px; line-height: 34px; }
  .card--back .brand-name { top: 60px; font-size: 22px; line-height: 28px; }

  .wave-band {
    position: absolute; left: 0; right: 0; bottom: 0;
    height: 36px;
  }
  .card--front .wave-band {
    background:
      linear-gradient(180deg, var(--card) 0%, rgba(241,241,241,0) 45%),
      linear-gradient(90deg, var(--sky), var(--royal), var(--azure), var(--royal), var(--sky));
  }
  .card--back .wave-band {
    bottom: 4px;
    height: 40px;
    background: linear-gradient(180deg, var(--card) 0%, var(--bars-grey) 100%);
  }

  .holder {
    position: absolute; right: 264px; top: 170px;
    text-align: right;
  }
  .holder-name { color: var(--royal); font-size: 21px; font-weight: 500; line-height: 26px; }
  .holder-role { color: var(--ink); font-size: 12px; line-height: 16px; margin-top: 2px; }

  .contact-list {
    position: absolute; left: 244px; top: 164px;
    list-style: none;
  }
  .contact-item {
    display: flex; align-items: center; gap: 10px;
    height: 18.5px;
    font-size: 12.5px; color: var(--ink);
    white-space: nowrap;
  }
  .contact-item svg { width: 11px; height: 11px; fill: var(--royal); flex: none; }
</style>
</head>
<body>
<main class="canvas">
  <section class="card card--front" aria-label="Card front">
    <p class="brand-name">Lumavelle Event Group</p>
    <div class="wave-band" role="img" aria-label="Blue sound wave equalizer bars pattern"></div>
  </section>

  <section class="card card--back" aria-label="Card back">
    <p class="brand-name">Lumavelle Event Group</p>
    <div class="holder">
      <p class="holder-name">Daniel Mercer</p>
      <p class="holder-role">Founder &amp; CEO</p>
    </div>
    <ul class="contact-list">
      <li class="contact-item">
        <svg viewBox="0 0 12 12" aria-hidden="true"><path d="M1 4c0-2 2-3 5-3s5 1 5 3v1H8.5V3.8H3.5V5H1z M3 6h6l1 5H2z"/></svg>
        555 0148 2260
      </li>
      <li class="contact-item">
        <svg viewBox="0 0 12 12" aria-hidden="true"><path d="M0 2h12v8H0z"/><path d="M0.5 2.5L6 7l5.5-4.5" stroke="#f1f1f1" stroke-width="1" fill="none"/></svg>
        daniel@lumavelle.example
      </li>
      <li class="contact-item">
        <svg viewBox="0 0 12 12" aria-hidden="true"><circle cx="6" cy="6" r="5.5"/><path d="M0.5 6h11M6 0.5v11M6 0.5c-3 3-3 8 0 11M6 0.5c3 3 3 8 0 11" stroke="#f1f1f1" stroke-width="0.8" fill="none"/></svg>
        www.lumavelle.example
      </li>
    </ul>
    <div class="wave-band" role="img" aria-label="Faint grey sound wave bars pattern"></div>
  </section>
</main>
</body>
</html>
```